International Clinical Software Company needs a new business card design

We are looking for a new business card design for our company that has recently expanded into the UK market, making us a multinational company.
After having rebranded our website and produced a new style guide, we are looking for a business card that is creative and attention grabbing, while being consistent with the style and colour scheme used on the new website, www.plumvora.example
We produce care management technology for the aged care market, but the main aspect we aim to communicate is the human element of our software, and the way it assists in providing better care for aged people, and stronger relationships between aged people and the staff that care for them.
Our current business card is a dark green with gold text, which makes the text quite difficult to read, not very aesthetically appealing and the colour scheme looks quite dated.
We would like something fresh and modern, that can still be colourful but doesn't use large blocks of dark colour, and uses the colours within our logo.
Something tying in with the leaves that are used in our logo could work quite nicely, along with the Autumn/Fall colours of soft greens, yellows and reds (also in our existing logo). However also happy to look at fresh, completely out of the box ideas we may not have yet considered.
Target Market(s)
The people that receive this business card work in the aged card or health industry and are either corporate/management level staff or clinical (Registered Nurses, care workers etc.)
Industry/Entity Type
Health Product
Contact Information for Business Card
Company Name - BrindlewayCare
Company locations: United Kingdom, Australia, New Zealand
Staff Details:
Staff name: Derek Mallow
Staff job title: Executive Chairman
Staff email: d.mallow@plumvora.example
Office phone number: 01742 918576
Font styles to use
Other font styles liked:
- Calibri
Requirements
Must have
- Must include the BrindlewayCare brand name in it's current font
- Must include logo (3 leaves in gold circle)
- Must include Business Card Details
Nice to have
- Elements of gold
- White space
- Something autumn themed but not too cliched
Should not have
- No blue - used by a major competitor and we would like to differentiate from them
- Large blocks of dark green colour (the green that appears in our leaves on the logo on our current business card is the background colour and it is far too dark)

```html
<!DOCTYPE html>
<html lang="en">
<head>
<meta charset="utf-8">
<title>BrindlewayCare – Business Card</title>
<link href="https://fonts.googleapis.com/css2?family=Arimo:wght@400;700&display=swap" rel="stylesheet">
<style>
  :root {
    --backdrop: #ecebe7;
    --card: #ffffff;
    --gold: #a8916a;
    --gold-light: #c9b48e;
    --crimson: #c2185b;
    --ink: #7a7a7a;
    --rule: #cfc6b5;
    --leaf-orange: #e8953a;
    --leaf-yellow: #f3cf6a;
    --leaf-red: #c9502c;
    --leaf-cream: #f7e7b4;
  }
  * { box-sizing: border-box; margin: 0; padding: 0; }
  html, body {
    width: 1200px; height: 950px; overflow: hidden;
    background: var(--backdrop);
    font-family: "Arimo", Arial, sans-serif;
  }
  .business-card {
    position: absolute; left: 100px; top: 190px;
    width: 1000px; height: 571px;
    background: var(--card);
    box-shadow: 0 10px 30px rgba(0,0,0,0.18);
    overflow: hidden;
  }
  .autumn-photo {
    position: absolute; right: 0; top: 0;
    width: 680px; height: 100%;
    background:
      radial-gradient(circle at 72% 30%, var(--leaf-cream) 0 12%, transparent 30%),
      radial-gradient(circle at 45% 12%, var(--leaf-red) 0 10%, transparent 26%),
      radial-gradient(circle at 85% 70%, var(--leaf-orange) 0 14%, transparent 34%),
      radial-gradient(circle at 60% 55%, var(--leaf-yellow) 0 18%, transparent 42%),
      linear-gradient(160deg, var(--leaf-orange), var(--leaf-yellow) 55%, var(--leaf-orange));
    -webkit-mask-image: linear-gradient(100deg, transparent 5%, rgba(0,0,0,0.45) 35%, #000 70%);
    mask-image: linear-gradient(100deg, transparent 5%, rgba(0,0,0,0.45) 35%, #000 70%);
    opacity: 0.85;
  }
  .brand {
    position: absolute; left: 70px; top: 80px;
    display: flex; flex-direction: column; align-items: flex-start; gap: 18px;
  }
  .brand-mark {
    width: 96px; height: 96px; border-radius: 50%;
    background: var(--gold-light);
    margin-left: 18px;
  }
  .brand-name {
    font-size: 54px; font-weight: 400; color: var(--gold);
    letter-spacing: 1px;
  }
  .contact {
    position: absolute; left: 70px; top: 300px;
  }
  .person-name { font-size: 32px; font-weight: 700; color: var(--gold); }
  .person-title { font-size: 25px; color: var(--crimson); margin-top: 4px; }
  .contact-list { list-style: none; margin-top: 10px; }
  .contact-list li {
    display: flex; align-items: center; gap: 12px;
    font-size: 24px; color: var(--ink); line-height: 36px;
  }
  .contact-list svg { width: 22px; height: 22px; fill: var(--gold); flex: none; }
  .locations {
    position: absolute; left: 560px; top: 330px;
    padding-left: 26px; border-left: 2px solid var(--rule);
    font-size: 24px; color: var(--ink); line-height: 36px;
  }
</style>
</head>
<body>
  <main class="business-card">
    <div class="autumn-photo" role="img" aria-label="Photograph of soft-focus autumn maple leaves in orange, yellow and red"></div>

    <div class="brand">
      <span class="brand-mark"></span>
      <span class="brand-name">BrindlewayCare</span>
    </div>

    <section class="contact">
      <h1 class="person-name">Derek Mallow</h1>
      <p class="person-title">Executive Chairman</p>
      <ul class="contact-list">
        <li>
          <svg viewBox="0 0 24 24" aria-hidden="true"><path d="M6.6 10.8a15 15 0 0 0 6.6 6.6l2.2-2.2a1 1 0 0 1 1-.25 11.4 11.4 0 0 0 3.6.57 1 1 0 0 1 1 1V20a1 1 0 0 1-1 1A17 17 0 0 1 3 4a1 1 0 0 1 1-1h3.5a1 1 0 0 1 1 1c0 1.25.2 2.46.57 3.6a1 1 0 0 1-.25 1z"/></svg>
          01742 918576
        </li>
        <li>
          <svg viewBox="0 0 24 24" aria-hidden="true"><path d="M2 5h20v14H2z M3.5 6.5 12 13l8.5-6.5" stroke="#fff" stroke-width="1.5"/></svg>
          d.mallow@plumvora.example
        </li>
        <li>
          <svg viewBox="0 0 24 24" aria-hidden="true"><circle cx="12" cy="12" r="10"/><path d="M2 12h20M12 2c3 3 3 17 0 20M12 2c-3 3-3 17 0 20" stroke="#fff" stroke-width="1.3" fill="none"/></svg>
          www.plumvora.example
        </li>
      </ul>
    </section>

    <address class="locations" style="font-style:normal">
      United Kingdom<br>
      Australia, New Zealand
    </address>
  </main>
</body>
</html>
```